Upmarket Dessert Lounge needs a Business Card Design

We are an upmarket dessert lounge needing a business card to match our image.

We want something that is simple yet beautiful, feminine, classy, sophisticated and elegant. We want it to stand out and don't mind if it is bold.

The design should include our logo and colours of red or maroon with gold highlights. We don't mind if black is used.

Marlow & Quince

Target Market(s)

For those who like to indulge or treat themselves and give in to their temptations on good quality desserts.

Industry/Entity Type

Business

Requirements
Must have
• Must include our logo and our name

Marlow & Quince

M & Q

```html
<!DOCTYPE html>
<html lang="en">
<head>
<meta charset="utf-8">
<title>Marlow &amp; Quince — Business Card</title>
<link rel="stylesheet" href="https://fonts.googleapis.com/css2?family=Libre+Baskerville:wght@400;700&family=Open+Sans:wght@400&display=swap">
<style>
  :root {
    --maroon: #7a1a1a;
    --maroon-deep: #5e1212;
    --gold: #f3d3a2;
    --ink: #3a3a3a;
    --rule: #9a9a9a;
    --card: #ffffff;
    --backdrop: #ece8e3;
  }
  * { box-sizing: border-box; margin: 0; padding: 0; }
  html, body { width: 1200px; height: 758px; overflow: hidden; }
  body {
    background: var(--backdrop);
    font-family: "Open Sans", Arial, sans-serif;
    color: var(--ink);
    position: relative;
  }
  .card {
    position: absolute;
    top: 229px;
    width: 520px;
    height: 300px;
    background: var(--card);
    border-radius: 30px;
    box-shadow: 0 6px 18px rgba(0,0,0,0.18);
  }
  .card--front { left: 50px; }
  .card--back { left: 630px; }

  .wordmark {
    position: absolute;
    left: 0; right: 0;
    text-align: center;
    font-family: "Libre Baskerville", Georgia, serif;
    font-weight: 400;
    color: var(--maroon);
    white-space: nowrap;
  }
  .card--front .wordmark { top: 52px; font-size: 30px; letter-spacing: 1px; }
  .card--back .wordmark { top: 70px; font-size: 72px; }

  .holder {
    position: absolute;
    top: 140px; left: 0; right: 0;
    text-align: center;
    font-family: "Libre Baskerville", Georgia, serif;
    font-size: 17px;
    color: var(--maroon);
  }
  .holder__name { font-weight: 700; letter-spacing: 1.5px; }
  .holder__title { font-size: 13px; color: var(--ink); font-family: "Open Sans", Arial, sans-serif; }

  .details {
    position: absolute;
    top: 196px; left: 0; right: 0;
    display: flex;
    justify-content: center;
    font-size: 12.5px;
    line-height: 17px;
  }
  .address {
    text-align: right;
    padding: 26px 12px 0 0;
    border-right: 1px solid var(--rule);
  }
  .contacts { list-style: none; padding-left: 10px; }
  .contacts li { display: flex; align-items: center; gap: 6px; }
  .contacts svg { width: 11px; height: 11px; fill: var(--ink); flex: none; }

  .web {
    position: absolute;
    top: 212px; left: 0; right: 0;
    text-align: center;
    font-size: 19px;
    letter-spacing: 2.5px;
    color: #222;
  }
</style>
</head>
<body>
  <section class="card card--front" aria-label="Card front">
    <div class="wordmark">MARLOW &amp; QUINCE</div>
    <p class="holder"><span class="holder__name">Your name,</span> <span class="holder__title">Title</span></p>
    <div class="details">
      <p class="address">Street Name, City Name<br>State Zip Code</p>
      <ul class="contacts">
        <li><svg viewBox="0 0 12 12" aria-hidden="true"><path d="M2.5 1l2 2-1 1.4c.7 1.5 1.8 2.6 3.1 3.1L8 6.5l2 2-1.3 1.8C5 10 2 7 1.7 2.3z"/></svg>555-201-4788</li>
        <li><svg viewBox="0 0 12 12" aria-hidden="true"><path d="M3.5 0.5h5v11h-5zM4.5 1.8v7.2h3V1.8z"/></svg>555-201-4788</li>
        <li><svg viewBox="0 0 12 12" aria-hidden="true"><path d="M0.5 2.5h11v7h-11zM1.5 3.3L6 6.6l4.5-3.3z"/></svg>hello@marlowquince.com</li>
        <li><svg viewBox="0 0 12 12" aria-hidden="true"><path d="M6 .8a5.2 5.2 0 100 10.4A5.2 5.2 0 006 .8zm0 1.2c.8.8 1.3 2.3 1.4 3.5H4.6C4.7 4.3 5.2 2.8 6 2zM2.1 6.5h1.5c.1 1.2.5 2.4 1.1 3.2A4 4 0 012.1 6.5zm0-1a4 4 0 012.6-3.2c-.6.8-1 2-1.1 3.2zm3.9 4.5c-.8-.8-1.3-2.3-1.4-3.5h2.8C7.3 7.7 6.8 9.2 6 10zm1.3-.3c.6-.8 1-2 1.1-3.2h1.5a4 4 0 01-2.6 3.2zM8.4 5.5c-.1-1.2-.5-2.4-1.1-3.2a4 4 0 012.6 3.2z"/></svg>www.marlowquince.com</li>
      </ul>
    </div>
  </section>

  <section class="card card--back" aria-label="Card back">
    <div class="wordmark">M &amp; Q</div>
    <p class="web">www.marlowquince.com</p>
  </section>
</body>
</html>
```